Theatre Company needs a Poster design for a world premiere of "The Lantern" Play.

We are premiering a play that celebrates community in rural and regional Australia . We need a poster for A3 and A5 size and an image that can be used in our email correspondence/webpage.

Attached is some ideas the producing theatre committee has come up with, a river runs through the town itself.

Town

```html
<!DOCTYPE html>
<html lang="en">
<head>
<meta charset="utf-8">
<title>The Lantern — Poster</title>
<link rel="stylesheet" href="https://fonts.googleapis.com/css2?family=Playfair+Display:ital,wght@0,400;1,400&family=Libre+Baskerville:wght@400&display=swap">
<style>
  :root {
    --sky: #cfd8dc;
    --sky-deep: #a9b6bc;
    --hill: #8e9a9f;
    --bank-light: #b7c0c3;
    --bank: #6f7b80;
    --grass-dark: #3a4449;
    --water: #1f2a31;
    --water-glint: #4a5760;
    --red: #c62f3c;
    --red-soft: rgba(198, 47, 60, 0.9);
    --white: #ffffff;
  }
  * { margin: 0; padding: 0; box-sizing: border-box; }
  html, body { width: 849px; height: 1200px; overflow: hidden; background: var(--white); }
  .poster {
    position: relative;
    width: 849px;
    height: 1200px;
    overflow: hidden;
  }
  .landscape {
    position: absolute;
    inset: 0;
    background:
      /* river channel winding from the middle distance toward the lower left */
      radial-gradient(ellipse 210px 120px at 560px 640px, var(--water-glint) 0%, rgba(74,87,96,0.6) 50%, transparent 100%),
      radial-gradient(ellipse 330px 200px at 470px 820px, var(--water) 0%, rgba(31,42,49,0.9) 55%, transparent 100%),
      radial-gradient(ellipse 420px 260px at 560px 1010px, var(--water) 0%, rgba(31,42,49,0.92) 60%, transparent 100%),
      /* grassy near bank, lower left */
      radial-gradient(ellipse 300px 420px at 60px 980px, #7d888c 0%, rgba(95,107,112,0.8) 45%, transparent 100%),
      /* pale far bank on the right */
      radial-gradient(ellipse 320px 110px at 760px 640px, var(--bank-light) 0%, rgba(183,192,195,0.7) 50%, transparent 100%),
      /* distant hills */
      radial-gradient(ellipse 260px 70px at 760px 430px, var(--hill) 0%, transparent 100%),
      radial-gradient(ellipse 180px 200px at 20px 330px, var(--hill) 0%, transparent 100%),
      /* cloud glow in the sky */
      radial-gradient(ellipse 240px 120px at 740px 290px, #eef2f3 0%, transparent 100%),
      linear-gradient(180deg, var(--sky-deep) 0%, var(--sky) 22%, #bcc6ca 34%, var(--hill) 42%, var(--bank) 56%, var(--grass-dark) 78%, #2a3338 100%);
  }
  .emblem {
    position: absolute;
    left: 20px;
    top: 84px;
    width: 650px;
    height: 650px;
  }
  .emblem svg { display: block; }
  .presenter {
    position: absolute;
    left: 38px;
    top: 292px;
    width: 590px;
    text-align: center;
    font-family: "Libre Baskerville", serif;
    font-size: 17px;
    letter-spacing: 0.2px;
    color: var(--white);
    white-space: nowrap;
  }
  .title {
    position: absolute;
    left: 28px;
    top: 366px;
    width: 633px;
    text-align: center;
    font-family: "Playfair Display", serif;
    font-weight: 400;
    font-size: 74px;
    line-height: 1;
    letter-spacing: 1px;
    color: var(--white);
    white-space: nowrap;
  }
  .credit {
    position: absolute;
    left: 28px;
    top: 506px;
    width: 592px;
    text-align: right;
    font-family: "Libre Baskerville", serif;
    font-size: 16.5px;
    color: var(--white);
    white-space: nowrap;
  }
  .tagline {
    position: absolute;
    left: 233px;
    top: 1099px;
    width: 602px;
    height: 72px;
    background: var(--red);
    border-top: 3px solid rgba(255,255,255,0.55);
    box-shadow: inset 0 4px 0 var(--red), inset 0 6px 0 rgba(255,255,255,0.35);
    display: flex;
    align-items: center;
    justify-content: center;
    font-family: "Playfair Display", serif;
    font-size: 28px;
    color: var(--white);
    white-space: nowrap;
  }
</style>
</head>
<body>
  <main class="poster">
    <div class="landscape" role="img" aria-label="Black and white photograph of a rural river winding between grassy banks toward distant hills under a cloudy sky"></div>

    <div class="emblem">
      <svg width="650" height="650" viewBox="0 0 650 650" aria-hidden="true">
        <circle cx="325" cy="325" r="325" fill="var(--red-soft)"/>
        <rect x="8" y="254" width="634" height="5" fill="var(--white)"/>
        <rect x="8" y="394" width="634" height="5" fill="var(--white)"/>
      </svg>
    </div>

    <p class="presenter">MURRAY BEND THEATRE COMPANY PRESENTS TO YOU</p>
    <h1 class="title">THE LANTERN</h1>
    <p class="credit">WRITTEN BY TESS WHITLOCK</p>

    <p class="tagline">“a river runs through the town itself”</p>
  </main>
</body>
</html>
```